Business Card Design

Lintel PR is a public relations consultancy service for the self build, home refurbishment and home improvement market.
It represents everything about 'home' so envisage logo featuring maybe roof pitch over the 'A' of Lintel. Colour/font undecided.

Industry/Entity Type

Home Improvement

Contact Information for Business Card

Fenna Corrowdale
fenna@lintelpr-mail.co.uk
Telephone Direct: 0712 645 8219

```html
<!DOCTYPE html>
<html lang="en">
<head>
<meta charset="utf-8">
<title>Lintel PR — Business Card</title>
<link rel="stylesheet" href="https://fonts.googleapis.com/css2?family=Exo+2:wght@400;500&display=swap">
<style>
  :root {
    --stage: #ecebe8;
    --card-white: #ffffff;
    --ink: #1c1c1c;
    --ink-soft: #2e2a24;
    --orange-light: #f6b41c;
    --orange-deep: #ec8a0c;
    --grey-band: #8a8a8c;
    --grey-light: #c9c9cb;
    --card-shadow: rgba(0, 0, 0, 0.14);
  }
  * { box-sizing: border-box; margin: 0; padding: 0; }
  html, body {
    width: 1200px; height: 800px; overflow: hidden;
    background: var(--stage);
    font-family: "Exo 2", "Segoe UI", sans-serif;
  }
  .canvas {
    position: relative; width: 1200px; height: 800px;
    display: flex; align-items: center; justify-content: center; gap: 60px;
  }
  .card {
    position: relative; width: 540px; height: 400px;
    background: var(--card-white);
    box-shadow: 0 6px 20px var(--card-shadow);
    overflow: hidden;
  }
  .card-art { position: absolute; inset: 0; width: 100%; height: 100%; }

  /* Front */
  .brand-lockup {
    position: absolute; left: 30px; top: 140px; width: 180px;
    display: flex; flex-direction: column; align-items: center; gap: 16px;
  }
  .brand-square { width: 70px; height: 70px; background: var(--ink); }
  .brand-name {
    font-weight: 500; font-size: 22px; letter-spacing: 3px;
    color: var(--ink); white-space: nowrap;
  }
  .details {
    position: absolute; right: 28px; top: 30px; width: 280px;
    text-align: right; color: var(--ink-soft);
  }
  .person-name { font-weight: 500; font-size: 19px; letter-spacing: 1.5px; text-transform: uppercase; }
  .person-role { font-weight: 500; font-size: 13px; letter-spacing: 1.5px; text-transform: uppercase; margin-top: 2px; }
  .address { font-size: 15px; line-height: 1.35; margin-top: 48px; padding-right: 30px; }
  .contact-list { list-style: none; margin-top: 40px; }
  .contact-list li {
    display: flex; justify-content: flex-end; align-items: center; gap: 8px;
    font-size: 13px; letter-spacing: 0.8px; height: 24px;
  }
  .contact-list svg { width: 16px; height: 16px; flex: none; }

  /* Back */
  .card-back { display: flex; align-items: center; justify-content: center; }
  .back-name {
    font-weight: 500; font-size: 46px; letter-spacing: 6px; color: var(--ink);
  }
</style>
</head>
<body>
<main class="canvas">

  <section class="card card-front" aria-label="Business card front">
    <svg class="card-art" viewBox="0 0 540 400" aria-hidden="true">
      <defs>
        <linearGradient id="orangeFill" x1="0" y1="0" x2="0.4" y2="1">
          <stop offset="0" stop-color="var(--orange-light)"/>
          <stop offset="1" stop-color="var(--orange-deep)"/>
        </linearGradient>
        <linearGradient id="greyFill" x1="0" y1="0" x2="1" y2="1">
          <stop offset="0" stop-color="var(--grey-light)"/>
          <stop offset="0.5" stop-color="var(--grey-band)"/>
          <stop offset="1" stop-color="var(--grey-light)"/>
        </linearGradient>
      </defs>
      <path d="M205 0 C300 70 300 270 160 400 L215 400 C345 280 345 80 278 0 Z" fill="url(#greyFill)"/>
      <path d="M272 0 L540 0 L540 400 L200 400 C330 285 340 85 272 0 Z" fill="#ffffff"/>
      <path d="M282 0 L540 0 L540 400 L212 400 C342 285 352 85 282 0 Z" fill="url(#orangeFill)"/>
    </svg>

    <div class="brand-lockup">
      <div class="brand-square"></div>
      <div class="brand-name">Lintel PR</div>
    </div>

    <div class="details">
      <p class="person-name">Fenna Corrowdale</p>
      <p class="person-role">Financial Advisor</p>
      <p class="address">14 Gable Yard,<br>Hearth Lane Road</p>
      <ul class="contact-list">
        <li>0712 645 8219
          <svg viewBox="0 0 16 16"><path d="M4 1.5l2.2 2.8-1.3 1.5c.8 1.8 2.2 3.2 4 4l1.5-1.3 2.8 2.2-1.4 2.3C6.5 12.5 3.5 9.5 2 4z" fill="var(--ink-soft)"/></svg>
        </li>
        <li>0712 645 8219
          <svg viewBox="0 0 16 16"><rect x="4.5" y="1" width="7" height="14" rx="1.2" fill="none" stroke="var(--ink-soft)" stroke-width="1.5"/><circle cx="8" cy="12.5" r=".9" fill="var(--ink-soft)"/></svg>
        </li>
        <li>0712 645 8219
          <svg viewBox="0 0 16 16"><rect x="2" y="6" width="12" height="8" fill="var(--ink-soft)"/><rect x="4.5" y="2" width="7" height="5" fill="none" stroke="var(--ink-soft)" stroke-width="1.3"/></svg>
        </li>
        <li>fenna@lintelpr-mail.co.uk
          <svg viewBox="0 0 16 16"><rect x="1.5" y="3.5" width="13" height="9" fill="none" stroke="var(--ink-soft)" stroke-width="1.4"/><path d="M1.5 3.5 8 9l6.5-5.5" fill="none" stroke="var(--ink-soft)" stroke-width="1.4"/></svg>
        </li>
        <li>www.lintelpr-studio.co.uk
          <svg viewBox="0 0 16 16"><circle cx="8" cy="8" r="6.3" fill="none" stroke="var(--ink-soft)" stroke-width="1.3"/><ellipse cx="8" cy="8" rx="2.8" ry="6.3" fill="none" stroke="var(--ink-soft)" stroke-width="1.1"/><path d="M1.7 8h12.6" stroke="var(--ink-soft)" stroke-width="1.1"/></svg>
        </li>
      </ul>
    </div>
  </section>

  <section class="card card-back" aria-label="Business card back">
    <p class="back-name">Lintel PR</p>
  </section>

</main>
</body>
</html>
```